International oil and gas consultancy needs a business card design

We need a business card design for a new oil and gas consultancy business based in Perth Australia. This is a professional services business and needs a moderately conservative type of business card. The business card also needs to be simple and uncluttered. The colour of the business logo is dark red (see attached file).
The front of the card should have a white background and mainly black lettering and perhaps some use of dark red and/or grey (your choice).
The back of the card should have a light grey background with dark red, black and or both dark red & black lettering (your choice).
Please find attached a clear brief of how I would like the business card designed.
Updates

Hello Everyone, I have slightly modified the brief. The main change is to incorporate some dark red and grey colours into the card, while still keeping the black lettering dominant. I have made the changes in the attached detailed brief document. Regards

Please note, the front of the card must say Harbour Ledger Services (in addition to the logo).

Industry/Entity Type

Conservative

Requirements
Must have
• brief has been updated. please refer to attachment for details.

Front of the card MUST say Harbour Ledger Services (in addition to the logo)

```html
<!DOCTYPE html>
<html lang="en">
<head>
<meta charset="utf-8">
<title>Harbour Ledger Services – Business Card</title>
<link rel="stylesheet" href="https://fonts.googleapis.com/css2?family=Exo+2:wght@400;500;700&display=swap">
<style>
  :root {
    --brand-red: #8e1b1f;
    --card-white: #ffffff;
    --card-grey: #e3e2e0;
    --ink-dark: #222222;
    --ink-grey: #4a4a4a;
    --backdrop: #f6f5f3;
    --on-red: #ffffff;
  }
  * { box-sizing: border-box; margin: 0; padding: 0; }
  html, body {
    width: 1200px;
    height: 1085px;
    overflow: hidden;
    background: var(--backdrop);
    font-family: "Exo 2", "Segoe UI", sans-serif;
  }
  .sheet { position: relative; width: 1200px; height: 1085px; }
  .card {
    position: absolute;
    left: 150px;
    width: 900px;
    height: 430px;
    border-radius: 6px;
    overflow: hidden;
    box-shadow: 0 6px 18px rgba(0,0,0,0.14);
  }
  .card-front { top: 80px; background: var(--card-white); }
  .brand {
    position: absolute;
    left: 80px;
    top: 90px;
    display: flex;
    align-items: center;
    gap: 26px;
  }
  .brand-mark {
    width: 96px;
    height: 96px;
    background: var(--brand-red);
    flex: none;
  }
  .brand-name {
    color: var(--brand-red);
    font-weight: 700;
    font-size: 52px;
    line-height: 1.05;
    letter-spacing: 1px;
  }
  .holder {
    position: absolute;
    right: 80px;
    bottom: 80px;
    text-align: right;
  }
  .holder-name {
    color: var(--ink-dark);
    font-weight: 500;
    font-size: 34px;
    letter-spacing: 3px;
    text-transform: uppercase;
  }
  .holder-title {
    margin-top: 6px;
    color: var(--ink-grey);
    font-size: 27px;
    letter-spacing: 1px;
  }
  .card-back { top: 570px; background: var(--card-grey); }
  .card-back svg { position: absolute; inset: 0; }
  .tab-band { fill: var(--brand-red); }
  .icon-ring { fill: none; stroke: var(--on-red); stroke-width: 3; }
  .icon-line { fill: none; stroke: var(--on-red); stroke-width: 2.5; stroke-linecap: round; stroke-linejoin: round; }
  .icon-fill { fill: var(--on-red); }
  .contact-group {
    position: absolute;
    right: 170px;
    text-align: right;
    color: var(--ink-dark);
    font-size: 30px;
    line-height: 1.22;
    letter-spacing: 1px;
  }
  .contact-phone { top: 48px; }
  .contact-address { top: 160px; }
  .contact-web { top: 308px; color: var(--brand-red); }
</style>
</head>
<body>
<main class="sheet">
  <section class="card card-front" aria-label="Card front">
    <div class="brand">
      <div class="brand-mark"></div>
      <div class="brand-name">Harbour Ledger<br>Services</div>
    </div>
    <div class="holder">
      <div class="holder-name">Martin Hale</div>
      <div class="holder-title">Managing Director</div>
    </div>
  </section>

  <section class="card card-back" aria-label="Card back">
    <svg width="900" height="430" viewBox="0 0 900 430" aria-hidden="true">
      <path class="tab-band" d="M900 0 V430 H830 C830 410 790 400 790 345 C790 290 830 290 830 280 C830 270 790 265 790 215 C790 165 830 160 830 150 C830 140 790 135 790 85 C790 30 830 20 830 0 Z"/>
      <circle class="icon-ring" cx="845" cy="85" r="27"/>
      <path class="icon-line" d="M835 72 q-6 4 -2 14 q6 13 18 17 q8 2 11 -4 l-6 -6 q-4 4 -8 1 q-6 -4 -8 -10 q-2 -4 2 -6 z"/>
      <circle class="icon-ring" cx="845" cy="215" r="27"/>
      <path class="icon-line" d="M845 233 C835 220 833 214 833 208 A12 12 0 0 1 857 208 C857 214 855 220 845 233 Z"/>
      <circle class="icon-fill" cx="845" cy="208" r="4"/>
      <circle class="icon-ring" cx="845" cy="345" r="27"/>
      <circle class="icon-line" cx="845" cy="345" r="15"/>
      <ellipse class="icon-line" cx="845" cy="345" rx="6" ry="15"/>
      <path class="icon-line" d="M830 345 H860 M833 337 H857 M833 353 H857"/>
    </svg>
    <div class="contact-group contact-phone">013 482 5716<br>013 482 5716</div>
    <div class="contact-group contact-address">041, 12th floor,<br>Quay Street Road<br>WPT</div>
    <div class="contact-group contact-web">mail@harbourledger.com<br>harbourledger.com</div>
  </section>
</main>
</body>
</html>
```